Create a memorable Stationary for Security Software Company

Velbrantix is the worldwide leader in securing the Internet. Making Internet communications and critical data secure, reliable and available everywhere has been and continues to be our ongoing vision. We are committed to staying focused on real customer needs and to developing new and innovative security solutions that redefine the security landscape.

Industry/Entity Type

Internet

Font styles to use
Serif
Sans Serif
Script

Colors
0792cd
33a6d7
85cae6

```html
<!DOCTYPE html>
<html lang="en">
<head>
<meta charset="utf-8">
<title>Velbrantix Business Cards</title>
<link href="https://fonts.googleapis.com/css2?family=Open+Sans:wght@400;600;700&display=swap" rel="stylesheet">
<style>
  :root {
    --brand-blue: #0792cd;
    --mid-blue: #33a6d7;
    --light-blue: #85cae6;
    --ink: #4a4a4a;
    --paper: #ffffff;
    --backdrop: #eef2f4;
  }
  * { box-sizing: border-box; margin: 0; padding: 0; }
  html, body {
    width: 1200px; height: 1120px; overflow: hidden;
    background: var(--backdrop);
    font-family: "Open Sans", Arial, sans-serif;
  }
  .sheet {
    width: 1200px; height: 1120px;
    display: flex; flex-direction: column; align-items: center;
    justify-content: center; gap: 40px;
  }
  .card {
    width: 875px; height: 500px; position: relative; overflow: hidden;
    box-shadow: 0 6px 18px rgba(0,0,0,0.12);
  }

  /* Back side */
  .card-back { background: var(--brand-blue); }
  .card-back .wordmark-faint {
    position: absolute; top: 150px; left: 0; right: 0;
    display: flex; align-items: center; justify-content: center; gap: 20px;
  }
  .card-back .wordmark-faint .mark-dot {
    width: 56px; height: 56px; border-radius: 50%; background: var(--mid-blue);
  }
  .card-back .wordmark-faint span {
    font-size: 76px; font-weight: 700; color: var(--mid-blue);
  }
  .card-back .site-url {
    position: absolute; bottom: 80px; left: 0; right: 0; text-align: center;
    color: var(--paper); font-size: 26px; letter-spacing: 5px;
  }

  /* Front side */
  .card-front { background: var(--paper); }
  .card-front .wordmark {
    position: absolute; top: 72px; left: 0; right: 0;
    display: flex; align-items: center; justify-content: center; gap: 14px;
  }
  .card-front .wordmark .mark-dot {
    width: 40px; height: 40px; border-radius: 50%; background: var(--mid-blue);
  }
  .card-front .wordmark span {
    font-size: 54px; font-weight: 700; color: var(--mid-blue);
  }
  .name-band {
    position: absolute; top: 236px; left: 0; right: 0; height: 78px;
    border-top: 3px solid var(--brand-blue); border-bottom: 3px solid var(--brand-blue);
    padding: 5px 0;
  }
  .name-band .band-fill {
    height: 100%; background: var(--brand-blue);
    display: flex; align-items: center; justify-content: center;
    color: var(--paper); font-size: 28px;
  }
  .name-band .band-fill strong { font-weight: 700; margin-right: 8px; }
  .contacts {
    position: absolute; top: 360px; left: 0; right: 0;
    display: flex; justify-content: center;
  }
  .contact-col {
    font-size: 21px; color: var(--ink); line-height: 34px;
  }
  .contact-col.address { text-align: right; padding-right: 24px; border-right: 1px solid #d5d5d5; }
  .contact-col.lines { padding-left: 24px; }
  .contact-row { display: flex; align-items: center; gap: 10px; }
  .contact-col.address .contact-row { justify-content: flex-end; }
  .icon { width: 18px; height: 18px; flex: none; }
</style>
</head>
<body>
<main class="sheet">
  <section class="card card-back">
    <div class="wordmark-faint"><i class="mark-dot"></i><span>Velbrantix</span></div>
    <p class="site-url">www.velbrantix.com</p>
  </section>

  <section class="card card-front">
    <div class="wordmark"><i class="mark-dot"></i><span>Velbrantix</span></div>
    <div class="name-band"><div class="band-fill"><strong>Your Name,</strong> Title</div></div>
    <div class="contacts">
      <div class="contact-col address">
        <div class="contact-row">
          <svg class="icon" viewBox="0 0 20 20"><circle cx="10" cy="10" r="9" fill="var(--mid-blue)"/><path d="M7 5c1 0 1.5 2 1 2.5l-1 1c.5 1.5 2 3 3.5 3.5l1-1c.5-.5 2.5 0 2.5 1 0 1-1 2-2 2-3.5 0-7-3.5-7-7 0-1 1-2 2-2z" fill="#fff"/></svg>
          <span>012-345-6789</span>
        </div>
        <div>Street Name, City Name</div>
        <div>Zipcode-012345</div>
      </div>
      <div class="contact-col lines">
        <div class="contact-row">
          <svg class="icon" viewBox="0 0 20 20"><rect x="5" y="1" width="10" height="18" rx="2" fill="var(--mid-blue)"/><rect x="7" y="4" width="6" height="8" fill="#fff"/></svg>
          <span>012-345-6789</span>
        </div>
        <div class="contact-row">
          <svg class="icon" viewBox="0 0 20 20"><rect x="1" y="4" width="18" height="12" rx="1" fill="var(--mid-blue)"/><path d="M2 5l8 6 8-6" stroke="#fff" stroke-width="1.5" fill="none"/></svg>
          <span>info@velbrantix.com</span>
        </div>
        <div class="contact-row">
          <svg class="icon" viewBox="0 0 20 20"><circle cx="10" cy="10" r="9" fill="var(--mid-blue)"/><path d="M1 10h18M10 1c-4 4-4 14 0 18M10 1c4 4 4 14 0 18" stroke="#fff" stroke-width="1.3" fill="none"/></svg>
          <span>www.velbrantix.com</span>
        </div>
      </div>
    </div>
  </section>
</main>
</body>
</html>
```